Business card for a Exhibition booth fabrication company

Hi. My company would like to change our corporate name card. We are an events and Exhibition stand builder company. We would like our corporate name card to resonate what we do. I need someone to create something unique that relates to the industry that I am in. The graphic designer should be creative to incorporate the elements of my industry and try to blend in well in the design of the card. Our aim is to ensure that we are unique and our card can look different from our competitors.
Updates

Target Market(s)

Marketing and events manager from all companies

Contact Information for Business Card

The business card should have the following details:
Name
Job Title
Email
Website

Colors

Designer to choose colors to be used in the design.

Requirements
Must have
• The card must be look something that is relevant to the service that I am providing. My website is: www.velmora-buildworks.com
• You can see my website to get more information on what service that I am doing
Nice to have
• On the back of my card, I would like to have a globe image with the incorporation of my company logo. This is to indicate that my services can be done in any part of the world.

```html
<!DOCTYPE html>
<html lang="en">
<head>
<meta charset="utf-8">
<title>Velmora Buildworks – Business Card</title>
<link href="https://fonts.googleapis.com/css2?family=Source+Sans+3:wght@400;600;700&display=swap" rel="stylesheet">
<style>
  :root{
    --bg:#2b2b2d;
    --card:#ffffff;
    --ink:#4a4a4d;
    --ink-soft:#6d6d70;
    --band:#4b4b4e;
    --red:#e3222b;
    --rule:#cfcfd2;
    --map-a:#f1f1f2;
    --map-b:#dedee0;
  }
  *{box-sizing:border-box;margin:0;padding:0}
  html,body{width:1200px;height:900px;overflow:hidden}
  body{background:var(--bg);font-family:"Source Sans 3",Arial,sans-serif;position:relative}
  .card{position:absolute;left:300px;width:600px;height:343px;background:var(--card);border-radius:18px;overflow:hidden}
  .card--front{top:52px}
  .card--back{top:478px}
  .card svg.art{position:absolute;inset:0}
  .brand{display:flex;align-items:center;gap:10px;white-space:nowrap}
  .brand__dot{width:22px;height:22px;border-radius:50%;background:var(--red);flex:none}
  .brand__name{font-weight:600;color:var(--ink);text-transform:uppercase}
  .card--front .brand{position:absolute;left:40px;top:136px}
  .card--front .brand__name{font-size:17px;letter-spacing:1.6px}
  .divider{position:absolute;left:318px;top:46px;width:1px;height:118px;background:var(--rule)}
  .contact{position:absolute;left:342px;top:44px}
  .contact__name{color:var(--red);font-weight:700;font-size:18px;line-height:22px;letter-spacing:.3px;text-transform:uppercase}
  .contact__title{color:var(--ink-soft);font-size:15px;line-height:20px;margin-bottom:10px}
  .contact__line{display:flex;align-items:center;gap:8px;color:var(--ink);font-size:14px;line-height:20px}
  .contact__line svg{width:12px;height:12px;flex:none}
  .address{position:absolute;right:36px;bottom:30px;color:#fff;font-size:14px;letter-spacing:.2px}
  .world{position:absolute;left:110px;top:40px;width:420px;height:270px;border-radius:50% 50% 40% 40%/55% 55% 45% 45%;background:radial-gradient(ellipse at 55% 45%,var(--map-b),var(--map-a) 60%,rgba(255,255,255,0) 75%)}
  .card--back .brand{position:absolute;left:50%;top:50%;transform:translate(-50%,-50%);gap:14px}
  .card--back .brand__dot{width:30px;height:30px}
  .card--back .brand__name{font-size:26px;letter-spacing:2.5px}
</style>
</head>
<body>
  <section class="card card--front" aria-label="Front of business card">
    <svg class="art" viewBox="0 0 600 343" preserveAspectRatio="none" aria-hidden="true">
      <path d="M0 272 C160 300 400 262 600 206 L600 343 L0 343 Z" fill="var(--band)"/>
      <path d="M0 264 C160 292 400 254 600 198" fill="none" stroke="var(--red)" stroke-width="5"/>
      <path d="M60 256 C210 276 420 240 600 190" fill="none" stroke="var(--red)" stroke-width="1.6"/>
      <path d="M130 252 C260 266 440 232 600 184" fill="none" stroke="var(--red)" stroke-width="1"/>
    </svg>
    <div class="brand">
      <span class="brand__dot"></span>
      <span class="brand__name">Velmora Buildworks</span>
    </div>
    <div class="divider"></div>
    <div class="contact">
      <p class="contact__name">Daniel Reyes</p>
      <p class="contact__title">President</p>
      <p class="contact__line">
        <svg viewBox="0 0 12 12"><path d="M2.5 1 L4.5 1 L5.2 3.6 L4 4.6 C4.7 6.2 5.8 7.3 7.4 8 L8.4 6.8 L11 7.5 L11 9.5 C11 10.3 10.3 11 9.5 11 C5 10.6 1.4 7 1 2.5 C1 1.7 1.7 1 2.5 1 Z" fill="var(--red)"/></svg>
        +974 55501234
      </p>
      <p class="contact__line">
        <svg viewBox="0 0 12 12"><rect x="1" y="2.5" width="10" height="7" fill="var(--red)"/><path d="M1 2.5 L6 6.5 L11 2.5" fill="none" stroke="#fff" stroke-width="1"/></svg>
        info@velmora-buildworks.com
      </p>
      <p class="contact__line">
        <svg viewBox="0 0 12 12"><circle cx="6" cy="6" r="5" fill="none" stroke="var(--red)" stroke-width="1.2"/><ellipse cx="6" cy="6" rx="2" ry="5" fill="none" stroke="var(--red)" stroke-width="1"/><path d="M1 6 H11" stroke="var(--red)" stroke-width="1"/></svg>
        www.velmora-buildworks.com
      </p>
    </div>
    <p class="address">P.O. Box 4120, West Bay Street, Doha - Qatar</p>
  </section>

  <section class="card card--back" aria-label="Back of business card">
    <div class="world" role="img" aria-label="Faint grey world map behind the company name"></div>
    <div class="brand">
      <span class="brand__dot"></span>
      <span class="brand__name">Velmora Buildworks</span>
    </div>
  </section>
</body>
</html>
```